Business card for Crestline Bathrooms

Please design a business card for our bathroom renovation business. You can use my existing logo, but if you have an idea to modernize it, I would like to see it. Please see attached files first. I would like to use the blue and the orange theme. I like the concept of using the shower head in the logo. Please find following a design (or two) that I have been trying to create with my limited resources. That design was for a sign, but I was going to adopt it and use it as a business card as well. I like the concept of the water splash but I don’t think it “flows” nicely together with the logo. Another thought is that maybe creating the logo out of water splash could work and have a dramatic effect (like the water text and the butterfly picture attached with similar background instead of white). If the above doesn’t work I would like to see a modern simplified design. One of the attached files named as the unwanted business card has all the details that I want included in the business card. Please note that it is two sided.
Updates

I am very thankful for the designs that I have received, but they are very similar and only a couple of attempts to do something with the water splash as per my original brief. Modernizing the logo and having it made out of out of water splash with the orange as color accent could work and have a dramatic effect (like the water text and the butterfly picture attached with similar background instead of white). Please do not use the butterfly itself! This is just an example that images can be created out of water splash.

Contact Information for Business Card

all the details are on the unwonted business card file included

Colors
3176b5

Requirements
Nice to have
• Copied from the brief:
• ... maybe creating the logo out of water splash could work and have a dramatic effect (like the water text and the butterfly picture attached with similar background instead of white). Please do not use the butterfly itself!
Should not have
• I am getting designs with a butterfly. The butterfly picture was an example of creating something from a water splash. The butterfly itself has no association with anything other than the concept of creating a logo out of water splash. Sorry, I thought I was clear in the brief.

```html
<!DOCTYPE html>
<html lang="en">
<head>
<meta charset="utf-8">
<title>Crestline Bathrooms – Business Card</title>
<link rel="stylesheet" href="https://fonts.googleapis.com/css2?family=Roboto:wght@400;500&family=Roboto+Condensed:wght@700&display=swap">
<style>
  :root {
    --backdrop: #2b2b2b;
    --card-white: #f7f7f7;
    --brand-navy: #0b4675;
    --brand-coral: #ee7a6a;
    --text-grey: #555555;
    --rule-grey: #d6d6d6;
    --card-blue: #043f6a;
    --on-blue: #ffffff;
  }
  * { box-sizing: border-box; margin: 0; padding: 0; }
  html, body { width: 1200px; height: 960px; overflow: hidden; }
  body {
    background: var(--backdrop);
    font-family: "Roboto", Arial, sans-serif;
    position: relative;
  }
  .card {
    position: absolute;
    border-radius: 20px;
  }
  .card--front {
    left: 320px; top: 95px; width: 605px; height: 352px;
    background: var(--card-white);
  }
  .card--back {
    left: 320px; top: 493px; width: 600px; height: 342px;
    background: var(--card-blue);
    color: var(--on-blue);
    text-align: center;
  }
  .brand-name {
    position: absolute;
    left: 52px; top: 150px; width: 230px;
    text-align: center;
    font-family: "Roboto", Arial, sans-serif;
    font-weight: 500;
    font-size: 27px;
    line-height: 1.1;
    color: var(--brand-navy);
  }
  .brand-dot {
    display: inline-block;
    width: 12px; height: 12px;
    border-radius: 50%;
    background: var(--brand-coral);
    margin-bottom: 8px;
  }
  .divider {
    position: absolute;
    left: 284px; top: 105px;
    width: 1px; height: 162px;
    background: var(--rule-grey);
  }
  .contact {
    position: absolute;
    left: 314px; top: 106px;
    color: var(--text-grey);
    font-size: 14.5px;
    line-height: 18px;
  }
  .contact__name {
    font-family: "Roboto Condensed", Arial, sans-serif;
    font-weight: 700;
    font-size: 21px;
    color: var(--brand-navy);
    margin-bottom: 8px;
  }
  .contact__address { margin-bottom: 8px; }
  .contact__list { list-style: none; }
  .contact__list li { display: flex; align-items: center; gap: 8px; height: 19px; }
  .contact__list svg { width: 13px; height: 13px; fill: #333; flex: none; }
  .back-name {
    margin-top: 88px;
    font-weight: 500;
    font-size: 30px;
    letter-spacing: 0.5px;
  }
  .services {
    list-style: none;
    margin-top: 66px;
    font-size: 14.5px;
    line-height: 18px;
  }
  .badges {
    display: flex; justify-content: center; align-items: center;
    gap: 14px; margin-top: 22px;
  }
  .badge-seal { width: 26px; height: 30px; background: var(--on-blue); border-radius: 4px; }
  .badge-rule { width: 1px; height: 34px; background: var(--on-blue); }
  .badge-plate { width: 116px; height: 26px; background: var(--on-blue); border-radius: 2px; }
</style>
</head>
<body>
  <section class="card card--front">
    <div class="brand-name"><span class="brand-dot"></span><br>Crestline Bathrooms</div>
    <div class="divider"></div>
    <div class="contact">
      <h1 class="contact__name">DANIEL MARLOWE</h1>
      <p class="contact__address">PO Box 41<br>Harwood Vale 2740</p>
      <ul class="contact__list">
        <li><svg viewBox="0 0 24 24"><path d="M6.6 10.8a15.1 15.1 0 0 0 6.6 6.6l2.2-2.2c.3-.3.7-.4 1-.2 1.1.4 2.3.6 3.6.6.6 0 1 .4 1 1V20c0 .6-.4 1-1 1A17 17 0 0 1 3 4c0-.6.4-1 1-1h3.5c.6 0 1 .4 1 1 0 1.3.2 2.5.6 3.6.1.3 0 .7-.2 1z"/></svg>0400 555 218</li>
        <li><svg viewBox="0 0 24 24"><path d="M7 1h10a2 2 0 0 1 2 2v18a2 2 0 0 1-2 2H7a2 2 0 0 1-2-2V3a2 2 0 0 1 2-2zm0 3v14h10V4z"/></svg>5550 1947</li>
        <li><svg viewBox="0 0 24 24"><path d="M2 5h20v14H2zm2 2v.5l8 5 8-5V7l-8 5z"/></svg>daniel@crestlinebathrooms.com.au</li>
        <li><svg viewBox="0 0 24 24"><circle cx="12" cy="12" r="10"/></svg>crestlinebathrooms.com.au</li>
      </ul>
    </div>
  </section>

  <section class="card card--back">
    <p class="back-name">Crestline Bathrooms</p>
    <ul class="services">
      <li>Complete Bathroom Renovations &amp; Remodelling</li>
      <li>Highly Skilled &amp; Qualified Tradespeople</li>
      <li>Professional Service From Concept To Completion</li>
      <li>All Work Guaranteed</li>
    </ul>
    <div class="badges" role="img" aria-label="Industry association membership badges">
      <span class="badge-seal"></span>
      <span class="badge-rule"></span>
      <span class="badge-plate"></span>
    </div>
  </section>
</body>
</html>
```